Brightmoor - a website to encourage people to spend time in nature

I have a squarespace site with some content on it but the squarespace template doesn't completely suit my needs, I keep fiddling with the template but actually I need some professional help to get it looking the way I want and with the right 'mood'.
The website is for "Brightmoor" - it will be a blog where I write about the importance of nature for good health. I also want to use the website to market services such as outdoor coaching, retreats and walking workshops.
This has been in my head for a LONG time and I currently only use instagram for micro-blogs but it's time for me to get this moving. I've previously engaged other designers on branding for it but they just didn't get it quite the way that I wanted it and I wasn't completely happy with the results. It's been a process for me as to what I want but in the meantime I just didn't come back to the design aspect of it now. I'm looking for a designer who understands the purpose of the website, the ethos and can help me realise this into a design that's clean, clear and simple.

Please note that I have a domain (brightmoor.org) and a lot of content drafted on squarespace already. I have published it with password protection - password is brightmoor2020 - it still has some of the original template on it, but does have some content. Don't take it as anything to follow in particular, i am looking for fresh eyes and fresh ideas.

Target Market(s)

There are three main groups that I want to target - people who are suffering from stress and anxiety, people who treat them and parents who want to get their kids outside (thereby preventing stress and anxiety)

Contact Information for Business Card

Joan Petrie
Brightmoor
Telephone +44 7700 900417
brightmoor@mailvane.com

Logo Text

Brightmoor - if that. I have an idea that the logo should have a leaf on it somewhere, or maybe just be a leaf.

Coding

Coded - Design and coding required

Number of Pages Required

5+ page

Font styles to use
Serif
Sans Serif

Colors
add136
33b8a4
34a6d7
3377b5

Requirements
Must have
• Space for lots of images. The ability for me to edit the pages if I need to. Be user friendly. Look beautiful.
• For an idea of the images I use and the content I'm interested in writing about have a look at @brightmoor on instagram.
• That pop up about cookies so I am complying with data laws.
Should not have
• Must not be too 'busy' I'd like to avoid too much movement.

```html
<!DOCTYPE html>
<html lang="en">
<head>
<meta charset="utf-8">
<title>Brightmoor – Spending time in nature to feel better</title>
<link rel="stylesheet" href="https://fonts.googleapis.com/css2?family=Libre+Bodoni:wght@400;700&family=Poppins:wght@300;400&family=Oswald:wght@300&display=swap">
<style>
:root{
  --ink:#000;
  --paper:#fff;
  --mist:#dfe9ec;
  --mist-deep:#a9bfc3;
  --stone:#ececec;
  --slate:#1d2830;
  --slate-deep:#141c22;
  --text:#333;
  --rule:#555;
  --serif:"Libre Bodoni",Georgia,serif;
  --sans:"Poppins",Arial,sans-serif;
  --display:"Oswald",Arial,sans-serif;
}
*{box-sizing:border-box;margin:0;padding:0}
html,body{width:1200px;height:3640px;overflow:hidden}
body{position:relative;background:var(--paper);font-family:var(--sans);color:var(--text)}
.abs{position:absolute}

/* header */
.site-header{left:0;top:0;width:1200px;height:105px;background:var(--ink);z-index:5}
.menu-btn{left:143px;top:31px;width:50px;height:50px;border-radius:50%;background:var(--paper)}
.menu-btn span{position:absolute;left:15px;width:20px;height:3px;background:var(--ink);border-radius:2px}
.brand{font-family:var(--display);font-weight:300;color:var(--paper);letter-spacing:12px;font-size:50px;line-height:1}
.site-header .brand{left:0;width:1200px;text-align:center;top:26px}
.round-btn{top:31px;width:52px;height:52px;border:2px solid var(--paper);border-radius:50%}
.round-btn .dot{position:absolute;left:13px;top:13px;width:22px;height:22px;border:2px solid var(--paper);border-radius:50%}

/* hero */
.hero{left:0;top:105px;width:1200px;height:760px;background:linear-gradient(180deg,#6b4a35 0%,#c7773a 22%,#a8593a 45%,#6a4a48 65%,#3a2e30 100%)}
.hero-rule{left:390px;top:290px;width:420px;height:6px;border-radius:50%;background:var(--paper)}
.hero h1{left:0;width:1200px;top:325px;text-align:center;font-family:var(--display);font-weight:300;font-size:96px;letter-spacing:6px;color:var(--paper);line-height:1}
.hero .tagline{left:0;width:1200px;top:440px;text-align:center;font-size:21px;letter-spacing:2.5px;color:var(--paper)}
.pill{display:flex;align-items:center;justify-content:space-between;border-radius:30px;font-family:var(--serif);text-transform:uppercase;color:#222}
.pill i{width:20px;height:20px;border-radius:50%;background:#111;position:relative}
.pill i::after{content:"";position:absolute;left:5px;top:6px;width:6px;height:6px;border-right:2px solid #fff;border-top:2px solid #fff;transform:rotate(45deg)}
.hero .pill{left:514px;top:515px;width:155px;height:46px;background:var(--paper);padding:0 16px 0 20px;font-size:12px}
.dots{left:548px;top:599px;display:flex;gap:16px}
.dots b{width:14px;height:14px;border:2px solid var(--paper);border-radius:50%}
.dots b.on{width:18px;height:18px;margin-top:-2px;background:#ddd}

/* about */
.about{left:0;top:700px;width:1200px;height:580px}
.about h2,.section-title{font-family:var(--serif);font-weight:700;text-transform:uppercase;color:#222}
.about h2{left:187px;top:178px;font-size:40px;font-weight:400}
.about .rule{left:187px;top:236px;width:372px;height:1px;background:var(--rule)}
.about p{left:186px;top:258px;width:378px;font-size:12.4px;line-height:18px;text-align:justify;color:#222}
.outline-pill{border:1.5px solid #222;background:var(--paper);padding:0 8px 0 18px;font-size:9px}
.about .outline-pill{left:186px;top:427px;width:128px;height:38px}
.about .portrait{left:628px;top:140px;width:410px;height:400px;border-radius:48% 52% 46% 54%/50% 46% 54% 50%;background:radial-gradient(circle at 50% 40%,#d8d4cc,#7e8b96 55%,#4a5460)}

/* gallery */
.gallery{left:0;top:1279px;width:1200px;height:865px;background:var(--stone)}
.section-title{left:0;width:1200px;text-align:center;font-size:40px}
.gallery .section-title{top:62px}
.gallery .rule{left:352px;top:118px;width:490px;height:1px;background:var(--rule)}
.photo{position:absolute}
.gallery .outline-pill{left:540px;top:750px;width:121px;height:38px}

/* blog */
.blog{left:0;top:2144px;width:1200px;height:830px;background:linear-gradient(180deg,#243039 0%,var(--slate) 40%,var(--slate-deep) 100%)}
.blog .section-title{top:98px;color:var(--paper);font-size:40px}
.blog .rule{left:414px;top:152px;width:372px;height:1px;background:#bbb}
.card{top:194px;width:285px;height:381px;background:var(--paper)}
.card .photo{left:0;top:0;width:100%;height:192px}
.card .date{position:absolute;left:0;top:143px;width:50px;height:49px;background:#111;color:var(--paper);font-family:var(--serif);text-align:center;padding-top:7px;line-height:1}
.card .date small{font-size:9px;display:block}
.card .date strong{font-size:18px;font-weight:400}
.card h3{position:absolute;left:25px;top:212px;font-family:var(--serif);font-weight:400;font-size:14px;letter-spacing:.5px;color:#222}
.card p{position:absolute;left:25px;top:245px;width:245px;font-size:11.2px;line-height:16.5px;color:#333}
.card .more{position:absolute;left:25px;top:330px;height:28px;padding:0 9px;border:1px solid #888;font-family:var(--serif);font-size:10px;line-height:26px;color:#222}
.card .more.solid{background:#111;color:var(--paper);border-color:#111}
.bars{left:527px;top:615px;display:flex;gap:17px}
.bars b{width:34px;height:6px;background:#8a9196}
.bars b.on{background:var(--paper)}

/* newsletter */
.newsletter{left:0;top:2840px;width:1200px;height:482px}
.newsletter .section-title{top:196px;font-size:40px}
.newsletter .rule{left:204px;top:243px;width:784px;height:1px;background:var(--rule)}
.contact{left:178px;display:flex;gap:16px;align-items:flex-start}
.contact .ico{width:38px;height:38px;border-radius:50%;background:#111;margin-top:4px;position:relative}
.contact .label{font-family:var(--serif);font-size:20px;color:#222}
.contact .value{font-family:var(--serif);font-size:12px;color:#333}
.field{height:34px;border:1px solid #777;background:var(--paper);font-family:var(--serif);font-size:10.5px;padding:0 12px;line-height:32px;color:#444}
.subscribe{left:562px;top:365px;width:450px;height:42px;background:#000;color:var(--paper);font-family:var(--serif);font-size:17px;text-align:center;line-height:42px}

/* footer */
.site-footer{left:0;top:3322px;width:1200px;height:318px;background:var(--ink)}
.site-footer .brand{left:0;width:1200px;text-align:center;top:85px;font-size:48px}
.site-footer .rule{left:425px;top:165px;width:350px;height:1px;background:#555}
.follow{left:0;width:1200px;top:182px;display:flex;justify-content:center;gap:12px;align-items:center;font-family:var(--serif);font-size:18px;color:var(--paper)}
.follow b{width:24px;height:24px;border-radius:50%;border:2px solid var(--paper)}
.copyright{left:0;width:1200px;top:240px;text-align:center;font-family:var(--serif);font-size:11px;color:#ddd}
</style>
</head>
<body>

<header class="site-header abs">
  <div class="menu-btn abs"><span style="top:16px"></span><span style="top:24px"></span><span style="top:32px"></span></div>
  <div class="brand abs">BRIGHTMOOR</div>
  <div class="round-btn abs" style="left:921px"><span class="dot"></span></div>
  <div class="round-btn abs" style="left:991px">
    <svg width="48" height="48" viewBox="0 0 48 48"><circle cx="22" cy="22" r="8" fill="none" stroke="#fff" stroke-width="2.4"/><line x1="28" y1="28" x2="34" y2="34" stroke="#fff" stroke-width="2.6" stroke-linecap="round"/></svg>
  </div>
</header>

<section class="hero abs" role="img" aria-label="Sunset over a misty mountain valley with a grassy cliff">
  <div class="hero-rule abs"></div>
  <h1 class="abs">BRIGHTMOOR</h1>
  <p class="tagline abs">The practice of spending time in nature to feel better.</p>
  <a class="pill abs">Read More <i></i></a>
  <div class="dots abs"><b></b><b class="on"></b><b></b><b></b></div>
</section>

<svg class="abs" style="left:0;top:660px" width="1200" height="625" viewBox="0 0 1200 625">
  <path d="M0 150 C80 170 160 150 240 120 C330 80 380 20 470 16 C560 12 600 60 700 60 C800 60 880 90 940 140 C1000 190 1080 160 1200 130 L1200 625 L0 625Z" fill="#a9bfc3"/>
  <path d="M0 125 C60 135 120 140 200 120 C300 95 390 15 470 16 C560 18 620 55 720 60 C820 65 900 100 960 150 C1020 200 1100 200 1200 185 L1200 625 L0 625Z" fill="url(#mistFade)"/>
  <path d="M1010 205 C1060 170 1090 140 1140 140 C1170 140 1190 150 1200 150 L1200 200 C1150 210 1080 220 1010 205Z" fill="#1f1a1c"/>
  <defs><linearGradient id="mistFade" x1="0" y1="0" x2="0" y2="1"><stop offset="0" stop-color="#dbe6e9"/><stop offset="1" stop-color="#e4edf0"/></linearGradient></defs>
</svg>

<section class="about abs">
  <h2 class="abs">About Us</h2>
  <div class="rule abs"></div>
  <p class="abs">Welcome to Brightmoor. An investigation of how spending time in nature helps you to feel better - physically, mentally, spiritually. This started as a personal journey to counteract the effect of too many hours in artificially lit offices, too much stress and too little connection to the natural world. It became something of a mission. To help others re-find their connection to the natural world, and in the process, live better and feel better.</p>
  <a class="pill outline-pill abs">View More <i></i></a>
  <div class="portrait abs" role="img" aria-label="Hiker with a large backpack looking out over clouds from a hilltop"></div>
</section>

<section class="gallery abs">
  <h2 class="section-title abs">Photo Gallery</h2>
  <div class="rule abs"></div>
  <div class="photo" style="left:143px;top:153px;width:293px;height:314px;background:linear-gradient(135deg,#e7a3b6,#c8456e 55%,#7e2a3e)" role="img" aria-label="Pink cherry blossom in bloom"></div>
  <div class="photo" style="left:448px;top:153px;width:293px;height:237px;background:linear-gradient(135deg,#4f7a3a,#2f5a28 60%,#a8b48a)" role="img" aria-label="Ladybird on a green leaf"></div>
  <div class="photo" style="left:752px;top:153px;width:293px;height:314px;background:linear-gradient(180deg,#7fa9d6 0%,#b8cde0 18%,#5a5450 22%,#3b3632 100%)" role="img" aria-label="Small dog and long shadows on a sandy beach"></div>
  <div class="photo" style="left:143px;top:478px;width:293px;height:236px;background:linear-gradient(160deg,#b8c08a,#5d6a3e 55%,#6d5c48)" role="img" aria-label="Woodland path between tall trees"></div>
  <div class="photo" style="left:448px;top:400px;width:293px;height:314px;background:linear-gradient(180deg,#6a6d72,#4b4f55 60%,#3c3b3a)" role="img" aria-label="Child looking out to sea, seen from behind">
    <svg style="position:absolute;left:119px;top:130px" width="54" height="54" viewBox="0 0 54 54"><rect x="1" y="1" width="52" height="52" fill="none" stroke="#fff" stroke-width="1.5"/><path d="M27 14V40M14 27H40" stroke="#fff" stroke-width="2.5"/></svg>
  </div>
  <div class="photo" style="left:752px;top:478px;width:293px;height:236px;background:linear-gradient(180deg,#6d7d55,#4a4a36 50%,#5a4a9a 80%,#3a2f6c)" role="img" aria-label="Bluebells carpeting a forest floor"></div>
  <a class="pill outline-pill abs">View All <i></i></a>
</section>

<section class="blog abs" role="region" aria-label="Blog">
  <h2 class="section-title abs">Our Blog</h2>
  <div class="rule abs"></div>

  <article class="card abs" style="left:144px">
    <div class="photo" style="background:linear-gradient(180deg,#c9d3dd,#6e8a4c 45%,#b8483a 75%,#5d7a38)" role="img" aria-label="Person sitting among wildflowers"></div>
    <div class="date"><small>AUG</small><strong>18</strong></div>
    <h3>ON THE VERGE</h3>
    <p>Sometimes it's just the simple things. You can be in a mix of complexity and it'll be something simple that will jolt you back to the now...</p>
    <a class="more">READ MORE &#187;</a>
  </article>

  <article class="card abs" style="left:453px">
    <div class="photo" style="background:linear-gradient(160deg,#e6e9ec,#7d93b0 50%,#3d5a80)" role="img" aria-label="Blue sky with scattered clouds"></div>
    <div class="date"><small>APR</small><strong>30</strong></div>
    <h3>SKYTIME OVER SCREENTIME</h3>
    <p>This is the defining challenge of parenting in the 21st Century. It's a recurring theme in conversations I have with other parents, it's on news bulletins...</p>
    <a class="more solid">READ MORE &#187;</a>
  </article>

  <article class="card abs" style="left:760px">
    <div class="photo" style="background:linear-gradient(160deg,#e6e6e4,#bdbdb8 55%,#55463a)" role="img" aria-label="Bird nest on weathered wood"></div>
    <div class="date"><small>JUN</small><strong>17</strong></div>
    <h3>NOTES FROM THE NEST</h3>
    <p>As I've spent more time in nature over the last couple of years, I've started to see the lessons we can take from it, lessons writ large. There are two in particular...</p>
    <a class="more">READ MORE &#187;</a>
  </article>

  <div class="bars abs"><b></b><b class="on"></b><b></b></div>
</section>

<svg class="abs" style="left:0;top:2770px" width="1200" height="210" viewBox="0 0 1200 210">
  <path d="M0 120 C60 100 120 70 200 78 C290 88 380 150 500 170 C560 180 600 120 700 60 C800 5 900 0 980 30 C1060 60 1120 10 1200 0 L1200 210 L0 210Z" fill="#a9bfc3"/>
  <path d="M0 140 C70 125 140 95 210 100 C300 110 390 175 520 190 C600 198 640 140 730 90 C820 40 920 20 1000 45 C1080 70 1140 30 1200 20 L1200 210 L0 210Z" fill="#ececec"/>
</svg>

<section class="newsletter abs">
  <h2 class="section-title abs">Subscribe Our Newsletter</h2>
  <div class="rule abs"></div>
  <div class="contact abs" style="top:290px">
    <span class="ico"><svg width="38" height="38" viewBox="0 0 38 38"><path d="M12 10c2-1 3 0 4 3l1 2c0 1-1 2-2 3 1 3 3 5 6 6 1-1 2-2 3-2l2 1c3 1 4 2 3 4-1 2-3 3-5 2-7-2-12-7-14-14-1-2 0-4 2-5z" fill="#fff"/></svg></span>
    <div><div class="label">Call Us:</div><div class="value">+44 7700 900417</div></div>
  </div>
  <div class="contact abs" style="top:355px">
    <span class="ico"><svg width="38" height="38" viewBox="0 0 38 38"><text x="19" y="26" text-anchor="middle" font-family="Arial,sans-serif" font-size="22" fill="#fff">@</text></svg></span>
    <div><div class="label">Mail Us:</div><div class="value">brightmoor@mailvane.com</div></div>
  </div>
  <div class="field abs" style="left:562px;top:277px;width:222px">FIRST NAME</div>
  <div class="field abs" style="left:792px;top:277px;width:222px">LAST NAME</div>
  <div class="field abs" style="left:562px;top:321px;width:450px">EMAIL ADDRESS</div>
  <div class="subscribe abs">SUBSCRIBE</div>
</section>

<footer class="site-footer abs">
  <div class="brand abs">BRIGHTMOOR</div>
  <div class="rule abs"></div>
  <div class="follow abs">Follow Us On: <b></b></div>
  <p class="copyright abs">&#169; Copyright 2016. All Rights Reserved</p>
</footer>

</body>
</html>
```